Water Delivery Service Website

We are working with BrivoNessé. They are a water delivery company and in need of a new website design.
Some sites to use for inspiration:
https://www.pelmoriston.example/home
https://www.quintalbrook.example/en/home3
https://www.drevik.example
https://www.tormaxel.example
Thank you for taking the time to consider designing a website for us. We are web developers based in Stockton, CA, USA. Most of our projects go through the same process. Understanding this process may help you win a project with us. We custom-code all of our websites in-house. We don’t have any requirements as to what tools you use for your design, but we prefer Figma files. For any design that we label as four-stars, we send it to the client for review. The client picks the final design they want us to use. Once we complete this process, we will continue to show additional clients all the four-star sites and purchase them later. Your designs will have multiple chances to sell. For better chances of success, we ask that you follow these guidelines.
IMAGES:
If you use any images or icons in the design, we ask that you have a link to the asset so we can purchase the image/icon. Most of the designs we submit do not have the customer’s images on them unless they have some great images. Be creative; show us the feeling you are trying to portray with your image choices. Use any royalty-free site you choose. We subscribe to Vantrel and mainly use their images, but we can purchase images outside of Vantrel.
PLEASE NOTE: we will not submit designs to clients with watermarks on the images.
FONTS:
We ask that you identify the fonts used in the design. This can be done in a message if you want. We typically use Google Fonts and Vantrel Fonts.
CONTENT:
We're always open to different content and ideas. We often submit designs with stock images so the client can see our vision. We typically take pictures after the website launch to use their images with our vision. Lorem Ipsum is fine for paragraphs, but we ask that you write the headers in correct English. We want to be able to show the vision and identify the sections of the website.
INSPIRATION:
We typically add a couple of links in the brief of websites we like to help you get started in your design.
REVISIONS:
We do not often ask for revisions of the designs unless we see something in the design that may not appeal to the client. If there are slight changes that we want to make, we do that in the development process.
FEEDBACK:
We rarely give feedback on designs during the design process. We are working on many website projects and do not have the time to provide feedback. We usually respond if your request is well thought out and asks specific questions, but a note asking “feedback, please” usually goes unanswered.

```html
<!DOCTYPE html>
<html lang="en">
<head>
<meta charset="utf-8">
<title>BrivoNessé Water Delivery</title>
<link rel="stylesheet" href="https://fonts.googleapis.com/css2?family=Montserrat:wght@400;500;600;700;800&family=Open+Sans:wght@400;600;700&display=swap">
<style>
:root{
  --navy:#0f1d4a;
  --navy-deep:#0b1640;
  --blue:#1b8fe0;
  --blue-bright:#2aa6f0;
  --blue-dark:#1565c0;
  --ice:#e7f4fc;
  --text:#4a5468;
  --muted:#8a93a6;
  --white:#fff;
  --star:#f5a623;
}
*{box-sizing:border-box;margin:0;padding:0}
html,body{width:1200px;height:5188px;overflow:hidden}
body{font-family:"Open Sans",Arial,sans-serif;color:var(--text);background:var(--white);font-size:14px;line-height:1.6}
h1,h2,h3,h4,.btn,.nav a{font-family:"Montserrat",Arial,sans-serif}
section,header,footer{position:relative;width:1200px;overflow:hidden}
.btn{display:inline-block;background:var(--blue);color:var(--white);font-weight:700;font-size:12px;letter-spacing:.5px;text-transform:uppercase;padding:13px 26px;border-radius:30px;text-decoration:none}
.btn.navy{background:var(--navy)}
.section-title{font-size:40px;font-weight:800;color:var(--navy);text-align:center;line-height:1.2}
.section-title span{font-weight:500;color:var(--navy)}
.drop-mark{display:block;margin:0 auto;width:18px;height:24px}
.title-block{position:absolute;left:0;right:0;text-align:center}
.title-block .drop-mark{margin-bottom:10px}

/* top bar */
.topbar{height:32px;background:var(--navy);color:var(--white);font-size:12px;font-weight:600;position:relative}
.topbar .seg{position:absolute;top:8px;display:flex;align-items:center;gap:6px;line-height:16px}
.topbar .seg i{display:inline-block;width:11px;height:11px;background:var(--white);border-radius:2px}

/* header */
.header{height:128px;border-bottom:1px solid #e6ebf2}
.logo{position:absolute;left:88px;top:22px;display:flex;align-items:center;gap:10px}
.logo .dot{width:34px;height:34px;border-radius:50%;background:var(--blue)}
.logo .name{font-family:"Montserrat",sans-serif;font-weight:800;font-size:28px;color:var(--navy)}
.contact-box{position:absolute;top:22px;display:flex;align-items:center;gap:10px;white-space:nowrap}
.contact-box .ic{width:36px;height:36px;border-radius:6px;background:var(--blue);display:flex;align-items:center;justify-content:center}
.contact-box small{display:block;font-size:11px;color:var(--muted);line-height:1.2}
.contact-box b{display:block;font-size:12px;color:var(--navy);line-height:1.3}
.socials{position:absolute;top:28px;right:88px;display:flex;gap:8px}
.socials i{width:24px;height:24px;border-radius:50%;border:1.5px solid var(--navy)}
.nav{position:absolute;top:80px;left:88px;right:88px;display:flex;align-items:center;gap:26px}
.nav a{font-size:13px;font-weight:600;color:var(--navy);text-decoration:none}
.nav a.active{color:var(--blue);border-bottom:2px solid var(--blue);padding-bottom:4px}
.nav .btn{margin-left:auto;padding:11px 22px;font-size:12px;text-transform:none}

/* hero */
.hero{height:640px}
.hero-photo{position:absolute;inset:0;background:linear-gradient(100deg,#1b3a6a 0%,#35628f 40%,#8aa7be 70%,#c9d6de 100%)}
.hero-copy{position:absolute;left:110px;top:120px;color:var(--white)}
.hero-copy h1{font-size:52px;font-weight:800;line-height:1.15}
.hero-copy h1 span{font-weight:500;display:block}
.hero-copy .btn{margin-top:40px}
.hero-wave{position:absolute;left:0;bottom:0;width:1200px;height:170px}

/* how it works */
.how{height:780px}
.how .title-block{top:24px}
.steps{position:absolute;top:130px;left:100px;right:100px;display:flex;justify-content:space-between}
.step{width:300px;text-align:center}
.step svg{width:280px;height:356px;display:block;margin:0 auto}
.step h3{font-size:24px;font-weight:700;color:var(--navy);margin-top:24px;line-height:1.2}
.step p{font-size:13px;margin-top:8px;padding:0 20px}
.how .btn{position:absolute;left:0;right:0;margin:0 auto;width:max-content;top:672px}

/* splash bands */
.splash{height:140px;background:linear-gradient(180deg,#ffffff 0%,#9ccfee 40%,#2f7fc4 70%,#d8ecf9 100%)}
.splash.two{height:120px;background:linear-gradient(180deg,#ffffff 0%,#7fc0ea 45%,#2a78bf 70%,#e7f4fc 100%)}

/* about */
.about{height:620px}
.about .big-drop{position:absolute;left:270px;top:-30px;width:380px;height:520px}
.about .small-drop{position:absolute;left:100px;top:290px;width:210px;height:290px}
.badge{position:absolute;left:470px;top:230px;width:110px;height:110px;border-radius:50%;background:var(--blue);border:5px solid var(--white);color:var(--white);text-align:center;display:flex;flex-direction:column;justify-content:center;font-family:"Montserrat",sans-serif}
.badge b{font-size:30px;line-height:1}
.badge small{font-size:11px;font-weight:600;line-height:1.2}
.about-copy{position:absolute;left:664px;top:60px;width:470px}
.about-copy .eyebrow{font-family:"Montserrat",sans-serif;font-weight:700;color:var(--blue);font-size:15px;display:flex;align-items:center;gap:8px}
.about-copy h2{font-size:32px;font-weight:800;color:var(--navy);line-height:1.25;margin-top:10px;white-space:nowrap}
.about-copy h2 span{font-weight:500;display:block}
.about-copy h4{font-size:14px;font-weight:700;color:var(--blue);margin-top:16px}
.about-copy p{font-size:13px;margin-top:10px}
.about-copy .btn{margin-top:24px}

/* when */
.when{height:740px;background:var(--ice)}
.when .title-block{top:40px}
.cards{position:absolute;top:188px;left:88px;right:88px;display:grid;grid-template-columns:1fr 1fr;gap:30px 40px}
.card{height:236px;background:var(--white);display:flex;box-shadow:0 6px 24px rgba(15,29,74,.08)}
.card .photo{width:230px;height:100%;position:relative}
.card .photo .chip{position:absolute;right:-26px;top:88px;width:52px;height:52px;border-radius:50%;background:var(--blue);border:4px solid var(--white)}
.card .body{padding:34px 26px 0 48px;flex:1}
.card h3{font-size:18px;font-weight:700;color:var(--navy)}
.card p{font-size:13px;margin-top:10px}
.card a{display:inline-block;margin-top:16px;font-family:"Montserrat",sans-serif;font-size:12px;font-weight:700;color:var(--blue);text-decoration:none}

/* why */
.why{height:420px;background:linear-gradient(90deg,var(--blue-bright) 0%,var(--blue-dark) 55%,var(--navy) 100%);color:var(--white);text-align:center}
.why .section-title{color:var(--white);padding-top:62px}
.why .section-title span{color:var(--white)}
.why p.lead{width:860px;margin:14px auto 0;font-size:13px;opacity:.9}
.features{position:absolute;top:226px;left:110px;right:110px;display:flex;justify-content:space-between}
.feature{width:160px}
.feature svg{width:76px;height:96px;display:block;margin:0 auto}
.feature h4{font-size:12px;font-weight:700;margin-top:12px;text-transform:uppercase}

/* testimonials */
.reviews{height:832px;background:linear-gradient(180deg,#ffffff 0%,#eef7fd 100%)}
.reviews .water{position:absolute;left:0;right:0;top:0;height:260px;background:linear-gradient(180deg,#f6fbfe 0%,#cfe7f7 60%,#eef7fd 100%)}
.reviews .title-block{top:150px}
.quotes{position:absolute;top:286px;left:108px;right:108px;display:flex;justify-content:space-between}
.quote{width:300px;text-align:center}
.quote .box{background:var(--white);padding:24px 30px 60px;box-shadow:0 6px 24px rgba(15,29,74,.09);height:300px}
.quote.mid .box{margin-top:-24px}
.stars{color:var(--star);font-size:16px;letter-spacing:2px}
.qmark{font-family:"Montserrat",sans-serif;font-size:48px;font-weight:800;color:var(--blue);line-height:1;height:40px}
.quote .box p{font-size:13px;margin-top:12px}
.avatar{width:80px;height:80px;border-radius:50%;border:4px solid var(--white);margin:-40px auto 0;position:relative}
.quote h4{font-size:14px;font-weight:700;color:var(--navy);margin-top:8px}
.quote small{font-size:12px;color:var(--muted)}
.dots{position:absolute;top:756px;left:0;right:0;display:flex;justify-content:center;gap:8px}
.dots i{width:9px;height:9px;border-radius:50%;background:#c7d3e3}
.dots i.on{background:var(--navy)}

/* cta */
.cta{height:308px;background:linear-gradient(90deg,var(--blue-bright),var(--blue) 60%,#1c7fd2);color:var(--white);text-align:center}
.cta h2{font-size:40px;font-weight:800;padding-top:66px;line-height:1.2}
.cta h2 span{font-weight:500}
.cta p{width:820px;margin:10px auto 0;font-size:13px}
.cta .btn{margin-top:28px}

/* footer */
.footer{height:380px;background:var(--navy-deep);color:#c4cce0;font-size:12px}
.footer .logo{left:108px;top:150px}
.footer .logo .name{color:var(--white)}
.fcol{position:absolute;top:56px}
.fcol h4{font-size:15px;font-weight:700;color:var(--white);text-transform:uppercase;margin-bottom:16px}
.fcol ul{list-style:none}
.fcol li{margin-bottom:8px;display:flex;align-items:flex-start;gap:8px}
.fcol li i{flex:none;width:12px;height:12px;border-radius:50%;background:var(--blue);margin-top:3px}
.subscribe{display:flex;margin-top:14px;width:300px}
.subscribe span{flex:1;background:var(--white);color:var(--muted);padding:9px 12px;font-size:12px;border-radius:3px 0 0 3px}
.subscribe b{width:42px;background:var(--blue);border-radius:0 3px 3px 0}
.fsocial{display:flex;gap:8px;margin-top:18px}
.fsocial i{width:30px;height:30px;border-radius:50%;background:var(--white)}
.bottom{position:relative;height:48px;background:#08112f;color:#aab4cc;font-size:12px}
.bottom .l{position:absolute;left:108px;top:15px}
.bottom .r{position:absolute;right:108px;top:15px}
</style>
</head>
<body>

<div class="topbar">
  <div class="seg" style="left:88px"><i></i>Residential</div>
  <div class="seg" style="left:190px"><i></i>Commercial</div>
</div>

<header class="header">
  <div class="logo"><span class="dot"></span><span class="name">BrivoNessé</span></div>
  <div class="contact-box" style="left:560px">
    <div class="ic"><svg width="18" height="18" viewBox="0 0 24 24"><path fill="#fff" d="M6.6 10.8a15 15 0 0 0 6.6 6.6l2.2-2.2c.3-.3.7-.4 1-.2 1.1.4 2.3.6 3.6.6.6 0 1 .4 1 1V20c0 .6-.4 1-1 1A17 17 0 0 1 3 4c0-.6.4-1 1-1h3.5c.6 0 1 .4 1 1 0 1.3.2 2.5.6 3.6.1.3 0 .7-.2 1z"/></svg></div>
    <div><small>Call Us</small><b>555-010-2040</b></div>
  </div>
  <div class="contact-box" style="left:710px">
    <div class="ic"><svg width="18" height="14" viewBox="0 0 24 18"><rect x="1" y="1" width="22" height="16" rx="2" fill="none" stroke="#fff" stroke-width="2"/><path d="M2 2l10 8 10-8" fill="none" stroke="#fff" stroke-width="2"/></svg></div>
    <div><small>Email Us</small><b>hello@brivonesse.example</b></div>
  </div>
  <div class="socials"><i></i><i></i><i></i><i></i></div>
  <nav class="nav">
    <a class="active">Home</a>
    <a>Water Delivery Options</a>
    <a>Our Services</a>
    <a>Private Label Bottled Water</a>
    <a>About</a>
    <a>Contact</a>
    <a>
      <svg width="10" height="13" viewBox="0 0 10 13" style="vertical-align:-1px"><path d="M5 0a5 5 0 0 1 5 5c0 3.5-5 8-5 8S0 8.5 0 5a5 5 0 0 1 5-5z" fill="#1b8fe0"/><circle cx="5" cy="5" r="1.8" fill="#fff"/></svg>
      Find Water</a>
    <a class="btn">Start Order</a>
  </nav>
</header>

<section class="hero">
  <div class="hero-photo" role="img" aria-label="Delivery worker in a blue uniform carrying a large water bottle to a smiling customer at her front door"></div>
  <div class="hero-copy">
    <h1>High-Quality<br>BrivoNessé Water<span>Delivery for Your Home</span></h1>
    <a class="btn">Get Water Delivery</a>
  </div>
  <svg class="hero-wave" viewBox="0 0 1200 170" preserveAspectRatio="none" aria-hidden="true">
    <path d="M0 90 C250 30 420 150 700 100 C900 60 1050 40 1200 70 L1200 170 L0 170 Z" fill="#cfe7f7"/>
    <path d="M0 120 C260 70 460 170 720 125 C930 90 1070 90 1200 110 L1200 170 L0 170 Z" fill="#fff"/>
  </svg>
</section>

<section class="how">
  <div class="title-block">
    <svg class="drop-mark" viewBox="0 0 18 24"><path d="M9 0S18 11 18 15a9 9 0 0 1-18 0C0 11 9 0 9 0z" fill="#1b8fe0"/></svg>
    <h2 class="section-title">How Water <span>Delivery Works</span></h2>
  </div>
  <div class="steps">
    <div class="step">
      <svg viewBox="0 0 200 254" role="img" aria-label="Man with a beard drinking a glass of water">
        <defs><linearGradient id="g1" x1="0" y1="0" x2="1" y2="1"><stop offset="0" stop-color="#c9b29a"/><stop offset="1" stop-color="#5c6e86"/></linearGradient></defs>
        <path d="M100 0C100 0 200 112 200 154A100 100 0 0 1 0 154C0 112 100 0 100 0Z" fill="url(#g1)"/>
      </svg>
      <h3>CHOOSE WATER</h3>
      <p>Lorem ipsum dolor sit amet, consectetur adipiscing elit, sed do eiusmod</p>
    </div>
    <div class="step">
      <svg viewBox="0 0 200 254" role="img" aria-label="Smiling delivery worker in a blue polo shirt">
        <defs><linearGradient id="g2" x1="0" y1="0" x2="1" y2="1"><stop offset="0" stop-color="#a9c9de"/><stop offset="1" stop-color="#2f6fa8"/></linearGradient></defs>
        <path d="M100 0C100 0 200 112 200 154A100 100 0 0 1 0 154C0 112 100 0 100 0Z" fill="url(#g2)"/>
      </svg>
      <h3>GET YOUR DELIVERY</h3>
      <p>Lorem ipsum dolor sit amet, consectetur adipiscing elit, sed do eiusmod</p>
    </div>
    <div class="step">
      <svg viewBox="0 0 200 254" role="img" aria-label="Person holding a glass of fresh water">
        <defs><linearGradient id="g3" x1="0" y1="0" x2="1" y2="1"><stop offset="0" stop-color="#7c8aa0"/><stop offset="1" stop-color="#2d3b55"/></linearGradient></defs>
        <path d="M100 0C100 0 200 112 200 154A100 100 0 0 1 0 154C0 112 100 0 100 0Z" fill="url(#g3)"/>
      </svg>
      <h3>DRINK UP!</h3>
      <p>Lorem ipsum dolor sit amet, consectetur adipiscing elit, sed do eiusmod</p>
    </div>
  </div>
  <a class="btn navy">Start Water Delivery &#10140;</a>
</section>

<div class="splash" role="img" aria-label="Wide band of splashing clear blue water"></div>

<section class="about">
  <svg class="big-drop" viewBox="0 0 200 274" role="img" aria-label="Delivery worker in a cap carrying a water jug on his shoulder">
    <defs><linearGradient id="g4" x1="0" y1="0" x2="1" y2="1"><stop offset="0" stop-color="#9fc6e4"/><stop offset=".6" stop-color="#1f4f85"/><stop offset="1" stop-color="#13284f"/></linearGradient></defs>
    <path d="M100 0C100 0 200 122 200 174A100 100 0 0 1 0 174C0 122 100 0 100 0Z" fill="url(#g4)"/>
  </svg>
  <svg class="small-drop" viewBox="0 0 200 274" role="img" aria-label="Hand holding a glass being filled with water">
    <defs><linearGradient id="g5" x1="0" y1="0" x2="1" y2="1"><stop offset="0" stop-color="#cfe3ef"/><stop offset="1" stop-color="#5e7f99"/></linearGradient></defs>
    <path d="M100 0C100 0 200 122 200 174A100 100 0 0 1 0 174C0 122 100 0 100 0Z" fill="url(#g5)"/>
  </svg>
  <div class="badge"><b>12+</b><small>Years Of<br>Experience</small></div>
  <div class="about-copy">
    <div class="eyebrow">About Us <svg width="14" height="19" viewBox="0 0 18 24"><path d="M9 0S18 11 18 15a9 9 0 0 1-18 0C0 11 9 0 9 0z" fill="#1b8fe0"/></svg></div>
    <h2>Try Our Water Today – No <span>Commitment Necessary</span></h2>
    <h4>Experience the Taste and Health Benefits of High-Quality BrivoNessé Water</h4>
    <p>Lorem ipsum dolor sit amet, consectetur adipiscing elit, sed do eiusmod tempor incididunt ut labore et dolore magna aliqua. Ut enim ad minim veniam, quis nostrud exercitation ullamco laboris nisi ut aliquip ex ea commodo consequat.</p>
    <p>Duis aute irure dolor in reprehenderit in voluptate velit esse cillum dolore eu fugiat nulla pariatur.</p>
    <a class="btn">Learn More</a>
  </div>
</section>

<div class="splash two" role="img" aria-label="Band of splashing water fading into light blue"></div>

<section class="when">
  <div class="title-block">
    <svg class="drop-mark" viewBox="0 0 18 24"><path d="M9 0S18 11 18 15a9 9 0 0 1-18 0C0 11 9 0 9 0z" fill="#1b8fe0"/></svg>
    <h2 class="section-title">How Water <span>When?</span></h2>
  </div>
  <div class="cards">
    <div class="card">
      <div class="photo" role="img" aria-label="Glass of purified water on a kitchen counter" style="background:linear-gradient(135deg,#e3e8ea,#8fa6b4)"><span class="chip"></span></div>
      <div class="body"><h3>Purified Water</h3><p>Lorem ipsum dolor sit amet, consectetur adipiscing elit, eiusmod tempor incididunt ut labore magna quis nostrud labore dolore.</p><a>SHOP NOW &#10140;</a></div>
    </div>
    <div class="card">
      <div class="photo" role="img" aria-label="Large spring water bottles on a cooler" style="background:linear-gradient(135deg,#d5e6f2,#4f86b4)"><span class="chip"></span></div>
      <div class="body"><h3>Spring Water</h3><p>Lorem ipsum dolor sit amet, consectetur adipiscing elit, eiusmod tempor incididunt ut labore magna quis nostrud labore dolore.</p><a>SHOP NOW &#10140;</a></div>
    </div>
    <div class="card">
      <div class="photo" role="img" aria-label="Bottles of distilled water by a window" style="background:linear-gradient(135deg,#f1dfc8,#5b7490)"><span class="chip"></span></div>
      <div class="body"><h3>Distilled Water</h3><p>Lorem ipsum dolor sit amet, consectetur adipiscing elit, eiusmod tempor incididunt ut labore magna quis nostrud labore dolore.</p><a>SHOP NOW &#10140;</a></div>
    </div>
    <div class="card">
      <div class="photo" role="img" aria-label="Alkaline water poured into a glass" style="background:linear-gradient(135deg,#e9eef2,#7994a8)"><span class="chip"></span></div>
      <div class="body"><h3>Alkaline Water</h3><p>Lorem ipsum dolor sit amet, consectetur adipiscing elit, eiusmod tempor incididunt ut labore magna quis nostrud labore dolore.</p><a>SHOP NOW &#10140;</a></div>
    </div>
  </div>
</section>

<section class="why">
  <h2 class="section-title">Why Choose <span>Us</span></h2>
  <p class="lead">Lorem ipsum dolor sit amet, consectetur adipiscing elit, sed do eiusmod tempor incididunt ut labore et dolore magna aliqua. Ut enim ad minim veniam, quis nostrud exercitation ullamco laboris nisi ut aliquip ex ea commodo consequat.</p>
  <div class="features">
    <div class="feature">
      <svg viewBox="0 0 76 96"><path d="M38 0S76 44 76 58a38 38 0 0 1-76 0C0 44 38 0 38 0z" fill="#fff"/><circle cx="38" cy="60" r="15" fill="none" stroke="#1565c0" stroke-width="3"/><path d="M38 51v9l6 4" fill="none" stroke="#1565c0" stroke-width="3" stroke-linecap="round"/></svg>
      <h4>Save Time</h4>
    </div>
    <div class="feature">
      <svg viewBox="0 0 76 96"><path d="M38 0S76 44 76 58a38 38 0 0 1-76 0C0 44 38 0 38 0z" fill="#fff"/><path d="M26 60l8 8 16-16" fill="none" stroke="#1565c0" stroke-width="4" stroke-linecap="round" stroke-linejoin="round"/></svg>
      <h4>Less Hassle</h4>
    </div>
    <div class="feature">
      <svg viewBox="0 0 76 96"><path d="M38 0S76 44 76 58a38 38 0 0 1-76 0C0 44 38 0 38 0z" fill="#fff"/><rect x="27" y="50" width="22" height="24" rx="2" fill="none" stroke="#1565c0" stroke-width="3"/><path d="M24 50h28M34 46h8" stroke="#1565c0" stroke-width="3" stroke-linecap="round"/></svg>
      <h4>Less Waste</h4>
    </div>
    <div class="feature">
      <svg viewBox="0 0 76 96"><path d="M38 0S76 44 76 58a38 38 0 0 1-76 0C0 44 38 0 38 0z" fill="#fff"/><path d="M24 48h28l-10 12v12l-8-4v-8z" fill="none" stroke="#1565c0" stroke-width="3" stroke-linejoin="round"/></svg>
      <h4>Best Filtration</h4>
    </div>
    <div class="feature">
      <svg viewBox="0 0 76 96"><path d="M38 0S76 44 76 58a38 38 0 0 1-76 0C0 44 38 0 38 0z" fill="#fff"/><path d="M32 46h12M34 46v10l-8 16h24l-8-16V46" fill="none" stroke="#1565c0" stroke-width="3" stroke-linejoin="round"/></svg>
      <h4>3rd Party Tested</h4>
    </div>
  </div>
</section>

<section class="reviews">
  <div class="water" role="img" aria-label="Soft splash of water across the top of the section"></div>
  <div class="title-block">
    <svg class="drop-mark" viewBox="0 0 18 24"><path d="M9 0S18 11 18 15a9 9 0 0 1-18 0C0 11 9 0 9 0z" fill="#1b8fe0"/></svg>
    <h2 class="section-title">What Our <span>Client Says</span></h2>
  </div>
  <div class="quotes">
    <div class="quote">
      <div class="box"><div class="stars">★★★★★</div><div class="qmark">&ldquo;</div><p>Sed ut perspiciatis unde omnis iste natus sit voluptatem accusantium doloremque laudantium, totam rem aperiam, eaque ipsa quae ab illo inventore veritatis et quasi architecto beatae vitae dicta sunt explicabo.</p></div>
      <div class="avatar" role="img" aria-label="Portrait of the reviewer" style="background:linear-gradient(135deg,#e2c6ad,#8d6e58)"></div>
      <h4>Maren Colvey</h4><small>1 month ago</small>
    </div>
    <div class="quote mid">
      <div class="box"><div class="stars">★★★★★</div><div class="qmark">&ldquo;</div><p>Sed ut perspiciatis unde omnis iste natus sit voluptatem accusantium doloremque laudantium, totam rem aperiam, eaque ipsa quae ab illo inventore veritatis et quasi architecto beatae vitae dicta sunt explicabo.</p></div>
      <div class="avatar" role="img" aria-label="Portrait of the reviewer" style="background:linear-gradient(135deg,#d9c2b0,#5a4c48)"></div>
      <h4>Idris Pallen</h4><small>1 month ago</small>
    </div>
    <div class="quote">
      <div class="box"><div class="stars">★★★★★</div><div class="qmark">&ldquo;</div><p>Sed ut perspiciatis unde omnis iste natus sit voluptatem accusantium doloremque laudantium, totam rem aperiam, eaque ipsa quae ab illo inventore veritatis et quasi architecto beatae vitae dicta sunt explicabo.</p></div>
      <div class="avatar" role="img" aria-label="Portrait of the reviewer" style="background:linear-gradient(135deg,#cfd9e3,#6b7f93)"></div>
      <h4>Lena Vorsk</h4><small>7 months ago</small>
    </div>
  </div>
  <div class="dots"><i></i><i class="on"></i><i></i><i></i></div>
</section>

<section class="cta">
  <h2>Water You Waiting For? <span>Spring into Action</span></h2>
  <p>Lorem ipsum dolor sit amet, consectetur adipiscing elit, sed do eiusmod tempor incididunt ut labore et dolore. Ut enim ad minim veniam, quis nostrud exercitation ullamco laboris nisi.</p>
  <a class="btn navy">Order Now</a>
</section>

<footer class="footer">
  <div class="logo"><span class="dot"></span><span class="name">BrivoNessé</span></div>
  <div class="fcol" style="left:392px">
    <h4>Quick Links</h4>
    <ul><li>Home</li><li>Water Delivery Options</li><li>Our Services</li><li>Private Label Bottled Water</li><li>About</li><li>Contact</li></ul>
  </div>
  <div class="fcol" style="left:592px">
    <h4>Contact Us</h4>
    <ul>
      <li><i></i>+1 555-010-2040</li>
      <li><i></i>hello@brivonesse.example</li>
      <li><i></i>Lorem ipsum dolor sit amet,<br>consectetur adipiscing elit</li>
      <li><i></i>(555) 010-7788</li>
    </ul>
  </div>
  <div class="fcol" style="left:832px">
    <h4>Subscribe to Our Blog</h4>
    <p style="width:290px">Sign up today to get news in your inbox and learn about our latest offers.</p>
    <div class="subscribe"><span>Enter your email</span><b></b></div>
    <div class="fsocial"><i></i><i></i><i></i><i></i></div>
  </div>
</footer>
<div class="bottom">
  <span class="l">Copyright 2025 brivonesse.example | All Rights Reserved</span>
  <span class="r">Terms and Conditions &nbsp;|&nbsp; Privacy Policy &nbsp;|&nbsp; Site Map</span>
</div>

</body>
</html>
```